Business card for a Exhibition booth fabrication company

Hi. My company would like to change our corporate name card. We are an events and Exhibition stand builder company. We would like our corporate name card to resonate what we do. I need someone to create something unique that relates to the industry that I am in. The graphic designer should be creative to incorporate the elements of my industry and try to blend in well in the design of the card. Our aim is to ensure that we are unique and our card can look different from our competitors.
Updates

Target Market(s)

Marketing and events manager from all companies

Contact Information for Business Card

The business card should have the following details:
Name
Job Title
Email
Website

Colors

Designer to choose colors to be used in the design.

Requirements
Must have
• The card must be look something that is relevant to the service that I am providing. My website is: www.velmora-buildworks.com
• You can see my website to get more information on what service that I am doing
Nice to have
• On the back of my card, I would like to have a globe image with the incorporation of my company logo. This is to indicate that my services can be done in any part of the world.

```html
<!DOCTYPE html>
<html lang="en">
<head>
<meta charset="utf-8">
<title>Velmora Buildworks – Business Card</title>
<link rel="stylesheet" href="https://fonts.googleapis.com/css2?family=Arimo:wght@400;700&family=Open+Sans:wght@400&display=swap">
<style>
  :root {
    --stage-light: #d9dadc;
    --stage-dark: #a3a4a7;
    --brand-red: #ed1c24;
    --ink-grey: #58595b;
    --swoosh-grey: #636466;
    --logo-grey: #6d6e71;
    --paper: #ffffff;
    --map-tint: rgba(255, 255, 255, 0.16);
  }
  * { margin: 0; padding: 0; box-sizing: border-box; }
  html, body { width: 1200px; height: 1119px; overflow: hidden; }
  body {
    background: linear-gradient(90deg, var(--stage-light), var(--stage-dark));
    position: relative;
    font-family: "Open Sans", sans-serif;
  }
  .card {
    position: absolute;
    left: 222px;
    width: 755px;
    height: 431px;
    border-radius: 36px;
    overflow: hidden;
  }
  .card--front { top: 100px; background: var(--paper); }
  .card--back { top: 587px; background: var(--brand-red); }

  .front-waves { position: absolute; inset: 0; width: 100%; height: 100%; }

  .holder { position: absolute; left: 49px; top: 62px; }
  .holder__name {
    font-family: "Arimo", sans-serif;
    font-weight: 700;
    font-size: 27px;
    color: var(--brand-red);
    letter-spacing: 0.3px;
  }
  .holder__title {
    font-family: "Arimo", sans-serif;
    font-size: 20px;
    color: var(--ink-grey);
    margin-top: 4px;
    letter-spacing: 0.5px;
  }

  .contacts { position: absolute; left: 48px; top: 150px; list-style: none; }
  .contacts__item {
    display: flex;
    align-items: center;
    height: 34px;
    font-size: 18px;
    color: var(--ink-grey);
  }
  .contacts__icon { width: 18px; height: 18px; margin-right: 13px; fill: var(--brand-red); }

  .brand {
    position: absolute;
    left: 395px;
    width: 336px;
    top: 180px;
    display: flex;
    align-items: center;
    justify-content: center;
    gap: 10px;
  }
  .brand__square { width: 16px; height: 16px; background: var(--brand-red); }
  .brand__name {
    font-family: "Arimo", sans-serif;
    font-weight: 700;
    font-size: 22px;
    letter-spacing: 1.6px;
    color: var(--logo-grey);
  }

  .front-address {
    position: absolute;
    left: 0; right: 0;
    top: 395px;
    text-align: center;
    font-size: 18px;
    color: var(--paper);
  }

  .world-map {
    position: absolute;
    left: 0; right: 0;
    top: 64px;
    height: 282px;
    background: radial-gradient(ellipse at 50% 45%, var(--map-tint), rgba(255,255,255,0.08) 70%, transparent 100%);
  }
  .back-brand {
    position: absolute;
    left: 0; right: 0;
    top: 272px;
    text-align: center;
    font-family: "Arimo", sans-serif;
    font-weight: 700;
    font-size: 29px;
    letter-spacing: 3px;
    color: #c9cacc;
  }
  .back-web {
    position: absolute;
    left: 0; right: 0;
    top: 391px;
    text-align: center;
    font-size: 20px;
    letter-spacing: 4.5px;
    color: var(--paper);
  }
</style>
</head>
<body>
  <section class="card card--front">
    <svg class="front-waves" viewBox="0 0 755 431" preserveAspectRatio="none">
      <path d="M0 250 C40 340 200 382 370 382 C510 382 610 322 755 300 L755 431 L0 431 Z" fill="var(--brand-red)"/>
      <path d="M2 240 C40 320 190 368 360 372 C500 374 620 318 755 290" fill="none" stroke="var(--paper)" stroke-width="10"/>
      <path d="M4 232 C45 312 190 362 360 366 C500 368 620 312 755 285" fill="none" stroke="var(--swoosh-grey)" stroke-width="6"/>
      <path d="M390 355 C520 330 640 298 755 272" fill="none" stroke="var(--brand-red)" stroke-width="1.5"/>
    </svg>

    <div class="holder">
      <h1 class="holder__name">DANIEL ROURKE</h1>
      <p class="holder__title">PRESIDENT</p>
    </div>

    <ul class="contacts">
      <li class="contacts__item">
        <svg class="contacts__icon" viewBox="0 0 24 24"><path d="M6.6 10.8a15.1 15.1 0 0 0 6.6 6.6l2.2-2.2c.3-.3.7-.4 1-.2 1.1.4 2.3.6 3.6.6.6 0 1 .4 1 1V20c0 .6-.4 1-1 1A17 17 0 0 1 3 4c0-.6.4-1 1-1h3.5c.6 0 1 .4 1 1 0 1.3.2 2.5.6 3.6.1.3 0 .7-.2 1z"/></svg>
        012-345-6789
      </li>
      <li class="contacts__item">
        <svg class="contacts__icon" viewBox="0 0 24 24"><path d="M2 5h20v14H2z M3.5 6.5 12 13l8.5-6.5" stroke="var(--paper)" stroke-width="1.6"/></svg>
        info@velmorabuildworks.com
      </li>
      <li class="contacts__item">
        <svg class="contacts__icon" viewBox="0 0 24 24"><g fill="none" stroke="var(--brand-red)" stroke-width="2"><circle cx="12" cy="12" r="9"/><ellipse cx="12" cy="12" rx="4" ry="9"/><path d="M3 12h18M5 7h14M5 17h14"/></g></svg>
        www.velmorabuildworks.com
      </li>
    </ul>

    <div class="brand">
      <span class="brand__square"></span>
      <span class="brand__name">VELMORA BUILDWORKS</span>
    </div>

    <p class="front-address">Street Name, City Name, Zipcode - 01234</p>
  </section>

  <section class="card card--back">
    <div class="world-map" role="img" aria-label="Faint world map spanning the card, showing services available worldwide"></div>
    <p class="back-brand">VELMORA BUILDWORKS</p>
    <p class="back-web">www.velmorabuildworks.com</p>
  </section>
</body>
</html>
```